Fenwick Grading LTD - website for irrigation & Landscape Lighting & Buried service wire

Looking for a website to help promote my business with Irrigation (installation, service, etc) and buried service wire/drainage solutions.

Commercial/Residential

Landscape lighting.

I’ll get photos in the trucks and trailers to upload as well maybe the machine as well.

Target Market(s)

Homeowners who want green grass and beautiful gardens. Beautiful landscape lighting

Industry/Entity Type

Irrigation systems and landscape lighting and buried service wire to homes and offering Drainage soltions.

Coding

Coded - Design and coding required

Number of Pages Required

4 page

Colors
F0912C
F2A743
F7CA91
FBE8D2
FDF5EE

Requirements
Must have
• was hoping to link up my email on fenwickgrading@mailbox-example.net with the website if possible.
Nice to have
• Page for Irrigation, page for landscape lighting, page buried service wire & drainage soltions.

```html
<!DOCTYPE html>
<html lang="en">
<head>
<meta charset="utf-8">
<title>Fenwick Grading LTD – Irrigation, Landscape Lighting &amp; Trenching</title>
<link href="https://fonts.googleapis.com/css2?family=Montserrat:wght@400;500;600;700&family=Varela+Round&display=swap" rel="stylesheet">
<style>
:root{
  --orange:#F0912C;
  --orange-2:#F2A743;
  --peach:#F7CA91;
  --cream:#FBE8D2;
  --ivory:#FDF5EE;
  --ink:#1d1d1d;
  --text:#444;
  --black:#000;
  --white:#fff;
}
*{margin:0;padding:0;box-sizing:border-box}
html,body{width:1200px;height:3922px;overflow:hidden}
body{position:relative;background:var(--white);font-family:"Montserrat",sans-serif;color:var(--ink)}
.abs{position:absolute}
.btn{position:absolute;display:flex;align-items:center;justify-content:center;border-radius:22px;background:var(--orange);color:var(--white);font-size:12px;font-weight:700;letter-spacing:.4px;text-transform:uppercase;text-decoration:none}
.btn-outline{background:var(--white);color:var(--orange);font-weight:600}

/* header */
.site-header{position:absolute;left:0;top:0;width:1200px;height:70px;z-index:5}
.brand{position:absolute;left:140px;top:24px;display:flex;align-items:center;gap:8px;font-size:17px;font-weight:700;color:var(--orange);white-space:nowrap}
.brand-dot{width:14px;height:14px;border-radius:50%;background:var(--orange)}
.nav{position:absolute;left:385px;top:27px;display:flex;gap:29px;font-size:13px;font-weight:500;white-space:nowrap}
.nav a{color:var(--ink);text-decoration:none}
.nav a.active{color:var(--orange);border-bottom:1px solid var(--orange);padding-bottom:2px}
.header-cta{left:938px;top:18px;width:119px;height:34px;border:1px solid var(--cream);box-shadow:0 2px 8px rgba(0,0,0,.12)}

/* hero */
.hero-band{position:absolute;left:0;top:70px;width:1200px;height:487px;background:var(--ivory)}
.hero-photo{position:absolute;left:0;top:0;z-index:1}
.hero-title{position:absolute;left:143px;top:176px;font-size:31px;line-height:48px;font-weight:500;color:var(--ink);z-index:2;white-space:nowrap}
.hero-title b{font-weight:700}
.hero-title .accent{color:var(--orange);font-weight:700}
.hero-lead{position:absolute;left:142px;top:334px;width:420px;padding-left:10px;border-left:2px solid var(--orange);font-size:12.5px;line-height:24px;font-weight:500;z-index:2}
.hero-btn{left:142px;top:404px;width:230px;height:38px;z-index:2}

/* services */
.service-photo{position:absolute}
.service-icon{position:absolute;width:64px;height:64px;border-radius:50%;background:var(--orange);display:flex;align-items:center;justify-content:center}
.service-title{position:absolute;font-family:"Varela Round",sans-serif;font-size:31px;color:var(--ink);font-weight:700;letter-spacing:.3px;white-space:nowrap}
.service-sub{position:absolute;width:390px;padding-left:10px;border-left:2px solid var(--orange);font-size:12.5px;line-height:20px;font-weight:600}
.service-text{position:absolute;width:390px;font-size:11.5px;line-height:22px;color:var(--text)}
.service-btn{width:120px;height:38px}

/* about */
.about{position:absolute;left:0;top:2144px;width:1200px;height:626px}
.about-panel{position:absolute;left:609px;top:84px;width:449px;height:454px;border-radius:10px;background:rgba(0,0,0,.8);border:1px solid rgba(255,255,255,.5);color:var(--white)}
.about-kicker{position:absolute;left:41px;top:50px;font-size:20px;font-weight:600}
.about-title{position:absolute;left:38px;top:90px;font-size:34px;font-weight:700;font-family:"Varela Round",sans-serif;white-space:nowrap}
.about-rule{position:absolute;left:41px;top:145px;width:61px;height:3px;background:var(--orange)}
.about-text{position:absolute;left:41px;top:170px;width:380px;font-size:11.5px;line-height:20.5px}
.about-text p+p{margin-top:8px}
.about-btn{left:38px;top:358px;width:110px;height:38px}

/* reviews */
.reviews-title{position:absolute;left:0;top:2852px;width:1200px;text-align:center;font-size:33px;font-weight:700;font-family:"Varela Round",sans-serif}
.reviews-rule{position:absolute;left:568px;top:2917px;width:64px;height:3px;background:var(--orange)}
.review-card{position:absolute;top:2974px;width:434px;height:252px;background:var(--white);box-shadow:0 2px 14px rgba(0,0,0,.1)}
.review-card::after{content:"";position:absolute;left:21px;right:21px;bottom:-7px;height:7px;background:#6c6c6c;border-radius:0 0 4px 4px}
.avatar{position:absolute;left:178px;top:-32px;width:78px;height:78px;border-radius:50%;border:3px solid var(--orange);background:linear-gradient(160deg,#cfc8c0,#8a7466)}
.review-name{position:absolute;left:0;top:63px;width:100%;text-align:center;font-size:18px;font-weight:600}
.review-text{position:absolute;left:30px;top:104px;width:374px;text-align:center;font-size:11.5px;line-height:21px;color:var(--text)}
.quote{position:absolute;right:14px;bottom:6px}
.slider-arrow{position:absolute;top:3080px;width:18px;height:30px}

/* cta */
.cta{position:absolute;left:190px;top:3314px;width:820px;height:247px;background:var(--orange);z-index:2}
.cta-frame{position:absolute;left:54px;top:43px;width:712px;height:143px;border:1px solid rgba(255,255,255,.75)}
.cta-title{position:absolute;left:0;top:80px;width:820px;text-align:center;color:var(--ink);font-size:31px;line-height:42px;font-family:"Varela Round",sans-serif;font-weight:700}
.cta-btn{left:354px;top:167px;width:111px;height:37px;font-size:11.5px}

/* footer */
.site-footer{position:absolute;left:0;top:3512px;width:1200px;height:410px;background:var(--black);color:var(--white)}
.footer-heading{position:absolute;top:112px;font-size:16px;font-weight:700}
.quick-links{position:absolute;left:143px;top:150px;list-style:none;font-size:12px}
.quick-links li{height:33px;display:flex;align-items:flex-start;gap:12px}
.quick-links li::before{content:"›";color:var(--white);font-size:13px;line-height:13px}
.contact-item{position:absolute;left:474px;display:flex;gap:14px}
.contact-icon{width:27px;height:27px;border-radius:50%;background:var(--orange);flex:none;display:flex;align-items:center;justify-content:center}
.contact-body{font-size:12px;line-height:20px;font-weight:500}
.contact-body b{font-weight:700;font-size:13px}
.footer-brand{position:absolute;left:857px;top:200px;width:220px;text-align:center;font-size:20px;font-weight:700;color:var(--orange);white-space:nowrap}
.socials{position:absolute;left:900px;top:260px;display:flex;gap:7px}
.socials span{width:28px;height:28px;border-radius:50%;border:1.5px solid var(--orange);display:block}
.footer-rule{position:absolute;left:140px;top:352px;width:920px;height:1px;background:#333}
.copyright{position:absolute;left:0;top:376px;width:1200px;text-align:center;font-size:11.5px;color:#ddd}
</style>
</head>
<body>

<div class="hero-band"></div>
<svg class="hero-photo" width="1200" height="557" viewBox="0 0 1200 557" role="img" aria-label="Lawn sprinkler spraying water over green grass at sunset">
  <defs>
    <linearGradient id="heroGrad" x1="0" y1="0" x2="0" y2="1">
      <stop offset="0" stop-color="#c9c07a"/>
      <stop offset=".45" stop-color="#8da94a"/>
      <stop offset="1" stop-color="#2f5a1c"/>
    </linearGradient>
  </defs>
  <path d="M850 0 C820 90 900 170 780 240 C620 320 610 410 720 400 C860 390 900 420 960 490 C1010 545 1100 560 1200 530 L1200 0 Z" fill="url(#heroGrad)"/>
  <path d="M642 370 C650 420 700 405 760 402 C870 398 905 430 962 495 C1012 552 1100 568 1200 535" fill="none" stroke="#F0912C" stroke-width="5"/>
</svg>

<header class="site-header">
  <div class="brand"><span class="brand-dot"></span>Fenwick Grading LTD</div>
  <nav class="nav">
    <a class="active" href="#">Home</a>
    <a href="#">Irrigation</a>
    <a href="#">Landscape Lighting</a>
    <a href="#">Fiber Optic Installation</a>
  </nav>
  <a class="btn btn-outline header-cta">Contact Us</a>
</header>

<h1 class="hero-title"><b>Welcome To</b> <span class="accent">Fenwick Grading</span><br>Your One-Stop Solution For<br>Home Improvement</h1>
<p class="hero-lead">Expertise In Irrigation Systems, Landscape Lighting, And Fiber Optic Installation</p>
<a class="btn hero-btn">Free No Obligation Quotes</a>

<!-- Irrigation -->
<svg class="service-photo" style="left:142px;top:676px" width="474" height="382" viewBox="0 0 474 382" role="img" aria-label="Pop-up sprinkler watering a lawn beside a gravel border">
  <defs><linearGradient id="g1" x1="0" y1="0" x2="1" y2="1"><stop offset="0" stop-color="#b9b1a4"/><stop offset=".5" stop-color="#6f9a3a"/><stop offset="1" stop-color="#8a7e6e"/></linearGradient></defs>
  <polygon points="0,0 474,0 237,370" fill="url(#g1)"/>
  <polyline points="0,12 237,382 474,12" fill="none" stroke="#F0912C" stroke-width="1.5"/>
</svg>
<div class="service-icon" style="left:675px;top:693px"><svg width="34" height="34" viewBox="0 0 34 34" fill="none" stroke="#fff" stroke-width="2"><rect x="8" y="18" width="5" height="12"/><rect x="21" y="18" width="5" height="12"/><path d="M4 30h26M10 15l-4-6M10 15l0-8M10 15l4-6M24 15l-4-6M24 15v-8M24 15l4-6"/></svg></div>
<h2 class="service-title" style="left:675px;top:764px">Irrigation Systems</h2>
<p class="service-sub" style="left:675px;top:812px">Efficient and Effective Watering Solutions for Your Lawn and Garden</p>
<p class="service-text" style="left:675px;top:860px">Our irrigation systems are designed to provide your lawn and garden with the right amount of water, without wasting a single drop. With our expert installation and service, you can rest assured that your plants will receive the nourishment they need to thrive.</p>
<a class="btn service-btn" style="left:675px;top:987px">Learn More</a>

<!-- Landscape lighting -->
<div class="service-icon" style="left:140px;top:1179px"><svg width="34" height="34" viewBox="0 0 34 34" fill="none" stroke="#fff" stroke-width="2"><path d="M10 28c-4-6-2-14 4-18M24 28c4-6 2-14-4-18M12 8l2-4M22 8l-2-4M8 30h18"/><circle cx="17" cy="16" r="4"/></svg></div>
<h2 class="service-title" style="left:140px;top:1250px">Landscape Lighting</h2>
<p class="service-sub" style="left:140px;top:1298px">Enhance Your Outdoor Space with Beautiful and Functional Lighting Solutions</p>
<p class="service-text" style="left:142px;top:1344px">Our landscape lighting solutions are designed to enhance the beauty and functionality of your outdoor space. From subtle pathway lighting to dramatic spotlights, we'll work with you to create a lighting plan that meets your needs and complements your landscape</p>
<a class="btn service-btn" style="left:140px;top:1480px;width:122px">Learn More</a>
<svg class="service-photo" style="left:585px;top:1159px" width="474" height="382" viewBox="0 0 474 382" role="img" aria-label="Garden at night lit by warm lights among trees">
  <defs><linearGradient id="g2" x1="0" y1="0" x2="0" y2="1"><stop offset="0" stop-color="#1f2d18"/><stop offset=".5" stop-color="#6c8a2e"/><stop offset="1" stop-color="#3d3a2a"/></linearGradient></defs>
  <polygon points="0,0 474,0 237,370" fill="url(#g2)"/>
  <polyline points="0,12 237,382 474,12" fill="none" stroke="#F0912C" stroke-width="1.5"/>
</svg>

<!-- Generic trenching -->
<svg class="service-photo" style="left:142px;top:1645px" width="474" height="382" viewBox="0 0 474 382" role="img" aria-label="Spade digging a trench in grass">
  <defs><linearGradient id="g3" x1="0" y1="0" x2="1" y2="1"><stop offset="0" stop-color="#4e7a2a"/><stop offset=".5" stop-color="#8a9e6a"/><stop offset="1" stop-color="#2f4f1c"/></linearGradient></defs>
  <polygon points="0,0 474,0 237,370" fill="url(#g3)"/>
  <polyline points="0,12 237,382 474,12" fill="none" stroke="#F0912C" stroke-width="1.5"/>
</svg>
<div class="service-icon" style="left:673px;top:1669px"><svg width="34" height="34" viewBox="0 0 34 34" fill="none" stroke="#fff" stroke-width="2"><circle cx="17" cy="11" r="6"/><path d="M17 17v8M9 28h16M12 25h10"/></svg></div>
<h2 class="service-title" style="left:673px;top:1742px">Generic Trenching</h2>
<p class="service-sub" style="left:673px;top:1789px">Lorem Ipsum Dolor Sit Amet, Consectetuer Adipiscing More Dollar Elit.</p>
<p class="service-text" style="left:673px;top:1836px">Duis autem vel eum iriure dolor in hendrerit in vulputate velit essen molestie consequat, vel illum dolore eu feugiat nulla facilisis at mk vero eros et accumsan et iust odio dignissim qui blandit praesent molestie consequat, vel illum dolore eu feugiat nulla facilisis at mk luptatum zzril delenit augue duis dolore te nulla facilisi.</p>
<a class="btn service-btn" style="left:673px;top:1966px">Learn More</a>

<!-- About -->
<section class="about">
  <svg class="abs" style="left:0;top:0" width="1200" height="626" viewBox="0 0 1200 626" role="img" aria-label="Suburban house with manicured lawn, hedges and red flower beds">
    <defs><linearGradient id="g4" x1="0" y1="0" x2="0" y2="1"><stop offset="0" stop-color="#5b7a3c"/><stop offset=".45" stop-color="#8e9688"/><stop offset=".75" stop-color="#3f6b22"/><stop offset="1" stop-color="#6da83a"/></linearGradient></defs>
    <rect width="1200" height="626" fill="url(#g4)"/>
  </svg>
  <div class="about-panel">
    <div class="about-kicker">About</div>
    <h2 class="about-title">Fenwick Grading LTD</h2>
    <div class="about-rule"></div>
    <div class="about-text">
      <p>Lorem ipsum dolor sit amet, consectetur adipiscing elit sed do eiusmod tempor incididunt ut labore et dolore magna aliqua Ut enim ad minim veniam quis</p>
      <p>Lorem ipsum dolor sit amet, consectetur adipiscing elit sed do eiusmod tempor incididunt ut labore et dolore magna aliqua Ut enim ad minim veniam quis "Lorem ipsum dolor sit amet, consectetur adipiscing elit sed do eiusmod tempor incididunt ut labore et dolore magna aliqua</p>
    </div>
    <a class="btn about-btn">Contact Us</a>
  </div>
</section>

<!-- Reviews -->
<h2 class="reviews-title">Customer Reviews</h2>
<div class="reviews-rule"></div>
<svg class="slider-arrow" style="left:136px" viewBox="0 0 18 30"><path d="M12 8l-6 7 6 7" fill="none" stroke="#555" stroke-width="2"/></svg>
<article class="review-card" style="left:143px">
  <div class="avatar" role="img" aria-label="Customer portrait"></div>
  <div class="review-name">Aaron Doe</div>
  <p class="review-text">Lorem Ipsum is simply dummy text of the printing and typesetting industry. Lorem Ipsum has been the industry's standard dummy text ever since the 1500s, when an unknown printer took a galley of type and scrambledstandard dummy text ever since standard dummy text ever since</p>
  <svg class="quote" width="42" height="34" viewBox="0 0 42 34" fill="#F7CA91"><path d="M2 2h16v16c0 8-4 13-12 14l-1-5c4-1 6-4 6-8H2zM24 2h16v16c0 8-4 13-12 14l-1-5c4-1 6-4 6-8h-9z"/></svg>
</article>
<article class="review-card" style="left:624px">
  <div class="avatar" role="img" aria-label="Customer portrait"></div>
  <div class="review-name">Mara Quill</div>
  <p class="review-text">Lorem Ipsum is simply dummy text of the printing and typesetting industry. Lorem Ipsum has been the industry's standard dummy text ever since the 1500s, when an unknown printer took a galley of type and scrambled standard dummy text ever since standard dummy text ever since</p>
  <svg class="quote" width="42" height="34" viewBox="0 0 42 34" fill="#F7CA91"><path d="M2 2h16v16c0 8-4 13-12 14l-1-5c4-1 6-4 6-8H2zM24 2h16v16c0 8-4 13-12 14l-1-5c4-1 6-4 6-8h-9z"/></svg>
</article>
<svg class="slider-arrow" style="left:1047px" viewBox="0 0 18 30"><path d="M6 8l6 7-6 7" fill="none" stroke="#F0912C" stroke-width="2"/></svg>

<!-- CTA -->
<section class="cta">
  <div class="cta-frame"></div>
  <h2 class="cta-title">Expertise In Irrigation Systems, Landscape<br>Lighting, And Fiber Optic Installation</h2>
  <a class="btn btn-outline cta-btn">Contact Us</a>
</section>

<!-- Footer -->
<footer class="site-footer">
  <h3 class="footer-heading" style="left:143px">Quick Links</h3>
  <ul class="quick-links">
    <li>Home</li><li>Irrigation</li><li>Landscape Lighting</li><li>Fiber Optic Installation</li><li>Contact Us</li>
  </ul>

  <h3 class="footer-heading" style="left:474px">Contact Details</h3>
  <div class="contact-item" style="top:150px">
    <span class="contact-icon"><svg width="12" height="14" viewBox="0 0 12 14" fill="#fff"><path d="M6 0a5 5 0 0 0-5 5c0 4 5 9 5 9s5-5 5-9a5 5 0 0 0-5-5zm0 7a2 2 0 1 1 0-4 2 2 0 0 1 0 4z"/></svg></span>
    <div class="contact-body">12 Lorem Imsum, Street Name,<br>City Name, Country – 12345</div>
  </div>
  <div class="contact-item" style="top:206px">
    <span class="contact-icon"><svg width="13" height="13" viewBox="0 0 13 13" fill="#fff"><path d="M3 0l2 3-1.5 1.5a8 8 0 0 0 5 5L10 8l3 2-1 2.5C6 13 0 7 .5 1z"/></svg></span>
    <div class="contact-body"><b>Phone</b><br>123.456.7890</div>
  </div>
  <div class="contact-item" style="top:262px">
    <span class="contact-icon"><svg width="13" height="10" viewBox="0 0 13 10" fill="none" stroke="#fff" stroke-width="1.5"><rect x=".75" y=".75" width="11.5" height="8.5"/><path d="M1 1l5.5 4.5L12 1"/></svg></span>
    <div class="contact-body"><b>Email</b><br>info@fenwickgrading-example.net</div>
  </div>

  <div class="footer-brand">Fenwick Grading LTD</div>
  <div class="socials"><span></span><span></span><span></span><span></span></div>

  <div class="footer-rule"></div>
  <p class="copyright">© 2024 Fenwick Grading LTD . All Rights Reserved.</p>
</footer>

</body>
</html>
```